Road Construction Company needs business cards

We would like a new business card designed for our business.

We're a road construction company based in Qld, Australia.

Can the business card please have the following information on it.

Name: Warren Halbeck
Position: General Manager
Phone: 0472 915 348
Email: Warren.halbeck@tovrin.com.au
Address: 87 Marrow Ave, Pendlebay, QLD, 4023
Website: www.tovrin.com.au

Visually we'd like the card to be professional and simple.

Attached is our logo.

Our website is www.tovrin.com.au

Target Market(s)

Men aged 25-60

Contact Information for Business Card

As listed in project description

Font styles to use
Serif

Requirements
Must have
• Large logo on back of card

```html
<!DOCTYPE html>
<html lang="en">
<head>
<meta charset="utf-8">
<title>Tovrin Road Construction – Business Card</title>
<link href="https://fonts.googleapis.com/css2?family=Open+Sans:wght@400;600;700;800&display=swap" rel="stylesheet">
<style>
  :root {
    --backdrop: #e6e6e6;
    --royal: #1356a4;
    --sky: #42a9dc;
    --ink: #000000;
    --paper: #ffffff;
  }
  * { margin: 0; padding: 0; box-sizing: border-box; }
  html, body { width: 1200px; height: 780px; overflow: hidden; }
  body {
    background: var(--backdrop);
    font-family: "Open Sans", Arial, sans-serif;
    position: relative;
  }
  .card {
    position: absolute;
    top: 240px;
    width: 525px;
    height: 300px;
    overflow: hidden;
    box-shadow: 0 4px 12px rgba(0,0,0,0.25);
  }
  .card-back { left: 50px; background: var(--royal); }
  .card-front { left: 625px; background: var(--ink); }

  .back-name {
    position: absolute;
    inset: 0;
    display: flex;
    align-items: center;
    justify-content: center;
    color: var(--paper);
    font-weight: 800;
    font-size: 84px;
    letter-spacing: 4px;
  }

  .front-name {
    position: absolute;
    top: 36px;
    left: 0; right: 0;
    text-align: center;
    color: var(--royal);
    font-weight: 800;
    font-size: 50px;
    letter-spacing: 3px;
  }

  .info-band {
    position: absolute;
    top: 150px;
    left: 0;
    width: 100%;
    height: 84px;
    display: flex;
  }
  .person {
    flex: 0 0 56%;
    background: var(--royal);
    color: var(--paper);
    text-align: right;
    padding: 18px 16px 0 0;
  }
  .person-name {
    font-weight: 700;
    font-size: 23px;
    line-height: 1.1;
    letter-spacing: 0.5px;
  }
  .person-role {
    font-size: 15px;
    font-weight: 400;
  }
  .contacts {
    flex: 1;
    background: var(--sky);
    color: var(--paper);
    list-style: none;
    padding: 10px 0 0 14px;
    font-size: 12.5px;
    line-height: 21px;
  }
  .contacts li { display: flex; align-items: center; gap: 7px; white-space: nowrap; }
  .contacts svg { width: 12px; height: 12px; flex: none; }

  .address {
    position: absolute;
    top: 248px;
    left: 0; right: 0;
    text-align: center;
    color: var(--paper);
    font-size: 15px;
  }
</style>
</head>
<body>
  <section class="card card-back" aria-label="Business card, back">
    <div class="back-name">TOVRIN</div>
  </section>

  <section class="card card-front" aria-label="Business card, front">
    <div class="front-name">TOVRIN</div>

    <div class="info-band">
      <div class="person">
        <div class="person-name">WARREN HALBECK</div>
        <div class="person-role">General Manager</div>
      </div>
      <ul class="contacts">
        <li>
          <svg viewBox="0 0 24 24" fill="#fff" aria-hidden="true"><path d="M6.6 10.8a15 15 0 0 0 6.6 6.6l2.2-2.2c.3-.3.7-.4 1-.2 1.1.4 2.3.6 3.6.6.6 0 1 .4 1 1V20c0 .6-.4 1-1 1A17 17 0 0 1 3 4c0-.6.4-1 1-1h3.5c.6 0 1 .4 1 1 0 1.3.2 2.5.6 3.6.1.3 0 .7-.2 1z"/></svg>
          0472 915 348
        </li>
        <li>
          <svg viewBox="0 0 24 24" fill="none" stroke="#fff" stroke-width="2" aria-hidden="true"><rect x="3" y="5" width="18" height="14" rx="1"/><path d="M3 6l9 7 9-7"/></svg>
          www.tovrin.com.au
        </li>
        <li>
          <svg viewBox="0 0 24 24" fill="none" stroke="#fff" stroke-width="2" aria-hidden="true"><circle cx="12" cy="12" r="9"/><path d="M3 12h18M12 3c3 3 3 15 0 18M12 3c-3 3-3 15 0 18"/></svg>
          Warren.halbeck@tovrin.com.au
        </li>
      </ul>
    </div>

    <div class="address">87 Marrow Ave, Pendlebay, QLD, 4023</div>
  </section>
</body>
</html>
```